Business Card Update, need to bring life to the card, two sided color

We need a new business card design, are moving and changing addresses and need a new look, we have the logos already attached but need a new style moving forward. Can incorporate the color of the logo (The Green) as well, maybe a solid back? We deal with safety products revolving around static electricity and safety lighting. Would like to keep same font in second logo as well.

Target Market(s)

Electrical Safety, Lighting

Contact Information for Business Card

Dale Fenwick
Vice President
Office: 770-555-4821
Cell: 770-555-3067
dale@tkfenwick.example
www.tkfenwick.example
4700 West Harbor Boulevard
Suite #150
Roswell, GA 30076

Font styles to use
Serif
Sans Serif

Requirements
Must have
• Since 1918
Nice to have
• Could use the 100 Year Logo for back of card, would like the back of card to be the same green as logo.
Should not have
• No black cards please.

```html
<!DOCTYPE html>
<html lang="en">
<head>
<meta charset="utf-8">
<title>T.K. Fenwick Business Card</title>
<link href="https://fonts.googleapis.com/css2?family=Arimo:wght@400;700&display=swap" rel="stylesheet">
<style>
  :root {
    --mint: #a3f5d2;
    --brand-green: #009455;
    --deep-green: #007a45;
    --forest: #0d3b27;
    --paper: #ffffff;
  }
  html, body {
    margin: 0;
    padding: 0;
    width: 1200px;
    height: 1200px;
    overflow: hidden;
    background: var(--mint);
    font-family: "Arimo", Arial, sans-serif;
  }
  .card {
    position: absolute;
    left: 222px;
    width: 757px;
    height: 462px;
    box-shadow: 3px 4px 5px rgba(0, 0, 0, 0.22);
    overflow: hidden;
  }
  .card-front { top: 126px; background: var(--paper); }
  .card-back {
    top: 612px;
    background: var(--brand-green);
    border: 18px solid var(--deep-green);
    box-sizing: border-box;
  }
  .card-art { position: absolute; inset: 0; }
  .brand-mark {
    position: absolute;
    left: 29px;
    top: 24px;
    width: 90px;
    height: 90px;
    border-radius: 50%;
    background: var(--brand-green);
  }
  .company-name {
    position: absolute;
    left: 130px;
    top: 44px;
    color: var(--brand-green);
    font-weight: 700;
    font-size: 29px;
    line-height: 1;
    margin: 0;
  }
  .company-type {
    position: absolute;
    left: 147px;
    top: 77px;
    color: var(--brand-green);
    font-weight: 700;
    font-size: 14px;
    letter-spacing: 0.4px;
    margin: 0;
  }
  .person {
    position: absolute;
    left: 32px;
    top: 138px;
    margin: 0;
  }
  .person-name {
    display: block;
    color: var(--forest);
    font-weight: 700;
    font-size: 22px;
    line-height: 1.2;
  }
  .person-title {
    display: block;
    color: var(--brand-green);
    font-weight: 700;
    font-size: 14px;
    letter-spacing: 0.4px;
    margin-top: 4px;
  }
  .contact-list {
    position: absolute;
    left: 330px;
    top: 296px;
    margin: 0;
    padding: 0;
    list-style: none;
    color: var(--paper);
    font-size: 15px;
    line-height: 1.25;
  }
  .contact-list li {
    display: flex;
    align-items: flex-start;
    margin-bottom: 7px;
  }
  .contact-icon { width: 20px; height: 18px; margin-right: 12px; flex: none; }
  .label { font-weight: 700; margin-right: 6px; }
  .back-brand {
    position: absolute;
    inset: 0;
    display: flex;
    flex-direction: column;
    align-items: center;
    justify-content: center;
    gap: 14px;
  }
  .back-mark {
    width: 120px;
    height: 120px;
    border-radius: 50%;
    background: var(--paper);
  }
  .back-name {
    color: var(--paper);
    font-weight: 700;
    font-size: 34px;
    margin: 4px 0 0;
  }
  .since {
    color: var(--paper);
    font-weight: 700;
    font-size: 16px;
    letter-spacing: 3px;
    text-transform: uppercase;
    margin: 0;
  }
</style>
</head>
<body>

<section class="card card-front">
  <svg class="card-art" viewBox="0 0 757 462" width="757" height="462" aria-hidden="true">
    <defs>
      <linearGradient id="circle-fade" x1="0" y1="0" x2="1" y2="0">
        <stop offset="0.35" stop-color="#009455"/>
        <stop offset="1" stop-color="#a6ccb0"/>
      </linearGradient>
      <linearGradient id="fold-shade" x1="0" y1="0" x2="1" y2="0">
        <stop offset="0" stop-color="#ffffff"/>
        <stop offset="1" stop-color="#bdb7b2"/>
      </linearGradient>
    </defs>
    <polygon points="570,0 595,0 555,40" fill="url(#fold-shade)"/>
    <polygon points="595,0 757,0 757,462 150,462" fill="var(--forest)"/>
    <polygon points="438,69 530,69 150,462 56,462" fill="var(--brand-green)"/>
    <polygon points="515,69 530,69 150,462 135,462" fill="var(--deep-green)" opacity="0.5"/>
    <circle cx="752" cy="236" r="80" fill="var(--brand-green)"/>
    <circle cx="736" cy="134" r="104" fill="url(#circle-fade)"/>
  </svg>

  <div class="brand-mark"></div>
  <h1 class="company-name">T.K. Fenwick</h1>
  <p class="company-type">Manufacturing Company, Inc.</p>

  <p class="person">
    <span class="person-name">Dale Fenwick</span>
    <span class="person-title">Vice President</span>
  </p>

  <ul class="contact-list">
    <li>
      <svg class="contact-icon" viewBox="0 0 24 22" aria-hidden="true">
        <path d="M7 2 L10 2 L11 7 L8.5 8.5 Q10 13 14 14.5 L15.5 12 L21 13 L21 17 Q20 20 16 19 Q5 16 3 5 Q3 2 7 2 Z" fill="#fff"/>
      </svg>
      <span><span class="label">Office</span>770-555-4821</span>
    </li>
    <li>
      <svg class="contact-icon" viewBox="0 0 24 22" aria-hidden="true">
        <rect x="6" y="0.5" width="12" height="21" rx="1.5" fill="none" stroke="#fff" stroke-width="2"/>
        <rect x="10" y="17" width="4" height="2" fill="#fff"/>
      </svg>
      <span><span class="label">Cell</span>770-555-3067</span>
    </li>
    <li>
      <svg class="contact-icon" viewBox="0 0 24 22" aria-hidden="true">
        <rect x="1" y="4" width="22" height="14" fill="#fff"/>
        <polyline points="1,4 12,12 23,4" fill="none" stroke="#0d3b27" stroke-width="2"/>
      </svg>
      dale@tkfenwick.example
    </li>
    <li>
      <svg class="contact-icon" viewBox="0 0 24 22" aria-hidden="true" fill="none" stroke="#fff" stroke-width="1.3">
        <circle cx="12" cy="11" r="10"/>
        <ellipse cx="12" cy="11" rx="4.5" ry="10"/>
        <line x1="2" y1="11" x2="22" y2="11"/>
        <line x1="4" y1="5.5" x2="20" y2="5.5"/>
        <line x1="4" y1="16.5" x2="20" y2="16.5"/>
      </svg>
      www.tkfenwick.example
    </li>
    <li>
      <svg class="contact-icon" viewBox="0 0 24 22" aria-hidden="true">
        <path d="M12 1 Q4 1 4 8.5 Q4 13 12 21 Q20 13 20 8.5 Q20 1 12 1 Z" fill="#fff"/>
        <circle cx="12" cy="8.5" r="3" fill="#0d3b27"/>
      </svg>
      <span>4700 West Harbor Boulevard, Suite #150<br>Roswell, GA 30076</span>
    </li>
  </ul>
</section>

<section class="card card-back">
  <div class="back-brand">
    <div class="back-mark"></div>
    <p class="back-name">T.K. Fenwick</p>
    <p class="since">Since 1918</p>
  </div>
</section>

</body>
</html>
```